A5 Flyer for Financial Services Business

I am after a re-design of our business flyer to fit in with our new branding style and logo colour scheme. Wanting something with a bit of designer flair that I could not create myself. I have included the flyer which I created which lacks style so dazzle me.

I want to use the same content.

Text for main body of flyer is

Are you a small business owner, tradie or TRPQ Service Provider struggling to stay on top of your bookkeeping and compliance obligations? If so we would love to help you get back on track and take control of your business finances so that you can make informed business decisions and focus on what you do best.

We have over 20 years industry experience and, as a small business ourselves, we are able to offer our clients a personal bookkeeping solution tailored to meet the needs of your business.

Accounts Payable | Accounts Receivable
Customer Invoicing
Bank and Credit Card Reconciliations
Payroll | Superannuation | Payroll Tax
Business Activity | Instalment Activity Statements
Regular Financial Reports
Vantly and Brimfolk Set-Up and Training

```html
<!DOCTYPE html>
<html lang="en">
<head>
<meta charset="utf-8">
<title>Evenkeel Financial Services – Bookkeeping Flyer</title>
<link href="https://fonts.googleapis.com/css2?family=Montserrat:wght@400;500;600;700;800&family=Roboto:wght@300&display=swap" rel="stylesheet">
<style>
:root{
  --navy:#0d3c5a;
  --navy-deep:#0a2f48;
  --teal:#12868a;
  --teal-band:#137d83;
  --teal-light:#2fb3b0;
  --ink:#14506e;
  --body:#333a40;
  --white:#ffffff;
  --bg:#b5b5b5;
  --star:#f2c230;
}
*{margin:0;padding:0;box-sizing:border-box}
html,body{width:1200px;height:2413px;overflow:hidden;background:var(--bg);font-family:"Montserrat",sans-serif}
.flyer{position:absolute;left:50px;top:425px;width:931px;height:1322px;background:var(--white);transform:scale(1.1815);transform-origin:0 0;overflow:hidden;box-shadow:0 6px 20px rgba(0,0,0,.25)}
.shapes{position:absolute;inset:0}
.brand{position:absolute;left:50px;top:130px;text-align:center;width:300px}
.brand-name{font-weight:500;font-size:31px;color:var(--teal);letter-spacing:-0.5px;line-height:1}
.brand-sub{font-family:"Roboto",sans-serif;font-weight:300;font-size:17px;letter-spacing:8px;color:#555;margin-top:6px}
.headline{position:absolute;left:50px;top:240px;color:var(--white);font-weight:800;font-size:44px;line-height:45px;letter-spacing:.3px}
.intro{position:absolute;left:50px;top:422px;width:540px}
.intro-q{color:var(--ink);font-weight:700;font-size:23.5px;line-height:29px}
.intro-p{color:var(--body);font-weight:500;font-size:21px;line-height:27px;margin-top:16px}
.experience{position:absolute;left:618px;top:360px;width:280px;color:var(--white)}
.stars{text-align:center;color:var(--star);font-size:26px;letter-spacing:4px;line-height:1;margin-left:-40px}
.exp-over{font-weight:500;font-size:23px;letter-spacing:2px;margin:14px 0 0 30px}
.exp-row{display:flex;align-items:center;margin:2px 0 0 26px}
.exp-num{font-weight:800;font-size:82px;line-height:78px;letter-spacing:-6px;color:var(--white)}
.exp-stack{margin-left:6px}
.exp-years{font-weight:800;font-size:38px;line-height:36px}
.exp-industry{font-weight:500;font-size:21px;letter-spacing:3px;line-height:22px}
.exp-tag{display:inline-block;background:var(--teal-light);font-weight:800;font-size:19px;padding:0 4px;line-height:24px;letter-spacing:.5px}
.exp-text{font-size:17.5px;line-height:22px;margin:14px 0 0 30px;width:225px;font-weight:400}
.exp-text b{font-weight:700}
.services{position:absolute;left:0;top:680px;width:931px;height:425px}
.service-col{position:absolute;top:22px;list-style:none}
.service-col.left{left:50px}
.service-col.right{left:495px}
.service{display:flex;align-items:center;height:65px;color:var(--white);font-weight:600;font-size:24px;line-height:27px}
.service svg{flex:none;width:56px;height:56px;margin-right:14px}
.contact-tab{position:absolute;left:0;top:1125px;width:350px;height:40px;background:var(--navy);color:var(--white);font-weight:800;font-size:25px;line-height:40px;padding-left:58px;letter-spacing:.5px;clip-path:polygon(0 0,100% 0,97% 100%,0 100%)}
.contact-line{position:absolute;left:50px;display:flex;align-items:center;color:#1e2326}
.contact-line svg{margin-right:10px}
.phone{top:1172px;font-weight:800;font-size:34px}
.email{top:1217px;font-weight:600;font-size:18.5px}
.web{top:1243px;font-weight:600;font-size:18.5px}
.badges{position:absolute;left:535px;top:1150px;display:flex;gap:6px}
.badge{width:110px;height:115px;border:2px solid #cfcfcf;border-radius:6px;display:flex;align-items:center;justify-content:center}
</style>
</head>
<body>
<main class="flyer">
  <svg class="shapes" viewBox="0 0 931 1322" width="931" height="1322" aria-hidden="false">
    <defs>
      <linearGradient id="bandGrad" x1="0" x2="1" y1="0" y2="0">
        <stop offset="0" stop-color="#0c3b5b"/>
        <stop offset="0.6" stop-color="#0f6478"/>
        <stop offset="1" stop-color="#13908c"/>
      </linearGradient>
      <linearGradient id="photoGrad" x1="0" x2="1" y1="0" y2="1">
        <stop offset="0" stop-color="#d9dfe3"/>
        <stop offset="0.5" stop-color="#eef1f3"/>
        <stop offset="1" stop-color="#b9c3ca"/>
      </linearGradient>
      <linearGradient id="badgeGrad" x1="0" x2="0" y1="0" y2="1">
        <stop offset="0" stop-color="#0f4868"/>
        <stop offset="1" stop-color="#0a2f48"/>
      </linearGradient>
    </defs>
    <polygon points="388,0 570,0 480,135" fill="#127d84"/>
    <polygon points="455,170 480,150 600,395 575,395" fill="#9aa3a8"/>
    <polygon role="img" aria-label="Photo of a smiling businessman at a desk reviewing financial documents with a colleague" points="570,0 931,0 931,395 600,395 480,150" fill="url(#photoGrad)"/>
    <polygon points="0,215 475,215 590,395 0,395" fill="url(#bandGrad)"/>
    <polygon points="604,395 755,318 903,395 903,680 604,680" fill="#1a9a98"/>
    <polygon points="612,398 755,328 895,398 895,680 612,680" fill="url(#badgeGrad)"/>
    <rect x="0" y="680" width="931" height="425" fill="var(--teal-band)"/>
    <line x1="452" y1="705" x2="452" y2="1080" stroke="#ffffff" stroke-opacity=".35" stroke-width="1.5"/>
    <rect x="535" y="1150" width="110" height="115" rx="6" fill="none"/>
  </svg>

  <div class="brand">
    <div class="brand-name">EVENKEEL</div>
    <div class="brand-sub">Financial Services</div>
  </div>

  <h1 class="headline">BOOKKEEPING<br>TAILORED TO YOUR<br>BUSINESS NEEDS</h1>

  <section class="intro">
    <p class="intro-q">Are you a small business owner, tradie or TRPQ Service Provider struggling to stay on top of your bookkeeping and compliance obligations?</p>
    <p class="intro-p">If so we would love to help you get back on track and take control of your business finances so that you can make informed business decisions and focus on what you do best.</p>
  </section>

  <aside class="experience">
    <div class="stars">★★★</div>
    <div class="exp-over">WE HAVE OVER</div>
    <div class="exp-row">
      <div class="exp-num">20</div>
      <div class="exp-stack">
        <div class="exp-years">YEARS</div>
        <div class="exp-industry">INDUSTRY</div>
        <div class="exp-tag">EXPERIENCE</div>
      </div>
    </div>
    <p class="exp-text">And, as a small business ourselves, we are able to offer our clients a <b>personal bookkeeping solution</b> tailored to meet the needs of your</p>
  </aside>

  <svg width="0" height="0" style="position:absolute">
    <symbol id="svc-icon" viewBox="0 0 56 56">
      <circle cx="28" cy="28" r="26" fill="none" stroke="#fff" stroke-width="1.6" stroke-dasharray="3 3"/>
      <circle cx="28" cy="28" r="21" fill="#fff"/>
      <rect x="19" y="16" width="18" height="24" rx="2" fill="none" stroke="#137d83" stroke-width="2"/>
      <line x1="23" y1="23" x2="33" y2="23" stroke="#137d83" stroke-width="2"/>
      <line x1="23" y1="28" x2="33" y2="28" stroke="#137d83" stroke-width="2"/>
      <line x1="23" y1="33" x2="30" y2="33" stroke="#137d83" stroke-width="2"/>
    </symbol>
  </svg>

  <section class="services">
    <ul class="service-col left">
      <li class="service"><svg><use href="#svc-icon"/></svg>Accounts Payable</li>
      <li class="service"><svg><use href="#svc-icon"/></svg>Accounts Receivable</li>
      <li class="service"><svg><use href="#svc-icon"/></svg>Customer Invoicing</li>
      <li class="service"><svg><use href="#svc-icon"/></svg>Bank and Credit Card<br>Reconciliations</li>
      <li class="service"><svg><use href="#svc-icon"/></svg>Payroll</li>
      <li class="service"><svg><use href="#svc-icon"/></svg>Superannuation</li>
    </ul>
    <ul class="service-col right">
      <li class="service"><svg><use href="#svc-icon"/></svg>Payroll Tax</li>
      <li class="service"><svg><use href="#svc-icon"/></svg>Business Activity</li>
      <li class="service"><svg><use href="#svc-icon"/></svg>Regular Financial Reports</li>
      <li class="service"><svg><use href="#svc-icon"/></svg>Instalment Activity<br>Statements</li>
      <li class="service"><svg><use href="#svc-icon"/></svg>Vantly and Brimfolk<br>Set-Up and Training</li>
    </ul>
  </section>

  <div class="contact-tab">CONTACT US TODAY</div>
  <div class="contact-line phone">
    <svg width="26" height="26" viewBox="0 0 24 24"><path d="M6.6 10.8a15 15 0 0 0 6.6 6.6l2.2-2.2c.3-.3.7-.4 1-.2 1.1.4 2.3.6 3.6.6.6 0 1 .4 1 1V20c0 .6-.4 1-1 1A17 17 0 0 1 3 4c0-.6.4-1 1-1h3.5c.6 0 1 .4 1 1 0 1.3.2 2.5.6 3.6.1.3 0 .7-.2 1z" fill="#137d83"/></svg>
    0491 570 110
  </div>
  <div class="contact-line email">
    <svg width="20" height="16" viewBox="0 0 20 16"><rect x="1" y="2" width="18" height="12" fill="#0d3c5a"/><path d="M1 2l9 7 9-7" stroke="#fff" stroke-width="1.5" fill="none"/></svg>
    hello@evenkeelfinancial.example.au
  </div>
  <div class="contact-line web">
    <svg width="20" height="20" viewBox="0 0 20 20"><circle cx="10" cy="10" r="8" fill="none" stroke="#137d83" stroke-width="2"/><ellipse cx="10" cy="10" rx="3.5" ry="8" fill="none" stroke="#137d83" stroke-width="1.5"/><line x1="2" y1="10" x2="18" y2="10" stroke="#137d83" stroke-width="1.5"/></svg>
    www.evenkeelfinancial.example.au
  </div>

  <div class="badges">
    <div class="badge" role="img" aria-label="Registration badge"><svg width="64" height="64"><circle cx="32" cy="32" r="30" fill="#e9e9e9"/></svg></div>
    <div class="badge" role="img" aria-label="Certification badge"><svg width="64" height="64"><rect x="6" y="6" width="52" height="52" rx="6" fill="#e9e9e9"/></svg></div>
    <div class="badge" role="img" aria-label="Partner badge"><svg width="80" height="64"><circle cx="40" cy="32" r="28" fill="#e9e9e9"/></svg></div>
  </div>
</main>
</body>
</html>
```